New Business Card Design Project

I need a design for business cards, i am an electrical business called "Corvane Electrical and Communications" i need the cards to be double sided with the company logo on the back (attached) the front needs to say my company name, web site, email address, telephone number, and ABN number and electrical license number. I am open to different arrangements of the information but would like the background to be incorporating something electrical or something that looks smart. open to all additional ideas also.

The company colours are orange and grey see logo attached.

Business Name: Corvane Electrical and Communications
Website: corvaneelectricalandcomms.example.com.au
Email: brent@corvaneelectricalandcomms.example.com.au
Telephone(mobile): 0481209736
ABN: 71208349162
Lic No: 418273D

Target Market(s)

Business entities, Project Managers, Accounts, Clients

Industry/Entity Type

Electrician

Contact Information for Business Card

I need a design for business cards, i am an electrical business called "Corvane Electrical and Communications" i need the cards to be double sided with the company logo on the back (attached) the front needs to say my company name

Font styles to use
Serif
Sans Serif

Colors
f37122
5c5c5c

Requirements
Must have
• Must have the Logo on the back open to different ways of it being on the back but had in mind to keep it central but again open to other options
Nice to have
• A real modern cool background that is eye catching yet contemporary
Should not have
• No backgrounds of a light bulb or plug or anything like that

```html
<!DOCTYPE html>
<html lang="en">
<head>
<meta charset="utf-8">
<title>Corvane Electrical and Communications – Business Cards</title>
<link href="https://fonts.googleapis.com/css2?family=Open+Sans:wght@400;600&display=swap" rel="stylesheet">
<style>
  :root {
    --stage: #2b2b2d;
    --card-black: #050505;
    --navy-deep: #070b16;
    --navy-mid: #0f1a33;
    --streak: #2e4a6a;
    --orange: #f5a623;
    --brand-orange: #f37122;
    --white: #ffffff;
    --soft-white: #e9e9e9;
  }
  * { box-sizing: border-box; margin: 0; padding: 0; }
  html, body { width: 1200px; height: 900px; overflow: hidden; }
  body {
    background: var(--stage);
    font-family: "Open Sans", Arial, sans-serif;
    position: relative;
  }
  .card {
    position: absolute;
    left: 260px;
    width: 680px;
    height: 389px;
    border-radius: 22px;
    overflow: hidden;
    box-shadow: 0 14px 30px rgba(0,0,0,.45);
  }
  .card--back { top: 40px; background: var(--card-black); }
  .card--front { top: 471px; background: var(--navy-deep); }

  .card__glow {
    position: absolute; inset: 0;
    background:
      radial-gradient(ellipse 45% 70% at 68% 42%, rgba(46,74,106,.75), transparent 70%),
      radial-gradient(ellipse 60% 50% at 40% 80%, rgba(15,26,51,.9), transparent 75%),
      linear-gradient(135deg, var(--navy-deep), var(--navy-mid) 55%, var(--navy-deep));
  }

  .band { position: absolute; left: 0; right: 0; bottom: 0; height: 52px; }
  .band__cell { position: absolute; }
  .band__left  { left: 0; width: 37%; bottom: 0; height: 24px; background: var(--orange); }
  .band__mid   { left: 37%; width: 33%; bottom: 0; height: 52px; background: var(--white); }
  .band__right { left: 70%; right: 0; bottom: 0; height: 52px; background: var(--orange); }

  .wordmark {
    position: absolute;
    display: flex; align-items: center; gap: 14px;
  }
  .wordmark__dot {
    width: 26px; height: 26px; border-radius: 50%;
    background: var(--orange); flex: none;
  }
  .wordmark__name {
    font-weight: 600; color: var(--white); line-height: 1.1;
  }
  .card--back .wordmark { left: 130px; top: 120px; }
  .card--back .wordmark__name { font-size: 34px; }
  .card--front .wordmark { left: 44px; top: 262px; }
  .card--front .wordmark__name { font-size: 22px; }

  .site-line {
    position: absolute; right: 30px; bottom: 62px;
    font-size: 17px; color: var(--white);
  }

  .person { position: absolute; right: 30px; top: 26px; text-align: right; }
  .person__name { font-size: 30px; color: var(--orange); letter-spacing: .5px; }
  .person__role { font-size: 11px; color: var(--white); letter-spacing: 1px; margin-top: 2px; }
  .rule {
    position: absolute; left: 36px; right: 30px; top: 80px;
    height: 1px; background: var(--soft-white); opacity: .8;
  }

  .contact {
    position: absolute; right: 30px; top: 150px;
    list-style: none; text-align: right;
    font-size: 14px; color: var(--white); line-height: 1.6;
  }
  .contact li { display: flex; justify-content: flex-end; align-items: center; gap: 10px; }
  .contact__label { color: var(--orange); }
  .contact svg { width: 14px; height: 14px; fill: var(--orange); flex: none; }
  .contact .noicon { padding-right: 24px; }

  .licence {
    position: absolute; right: 30px; bottom: 16px;
    font-size: 14px; color: var(--navy-deep);
  }
</style>
</head>
<body>

<section class="card card--back" aria-label="Card back">
  <div class="wordmark">
    <span class="wordmark__dot"></span>
    <span class="wordmark__name">Corvane Electrical<br>and Communications</span>
  </div>
  <p class="site-line">www.corvaneelectricalandcomms.example.com.au</p>
  <div class="band">
    <span class="band__cell band__left"></span>
    <span class="band__cell band__mid"></span>
    <span class="band__cell band__right"></span>
  </div>
</section>

<section class="card card--front" aria-label="Card front">
  <div class="card__glow" role="img" aria-label="Soft blue light streaks on a dark navy background"></div>

  <div class="person">
    <p class="person__name">MARLO TESSALY</p>
    <p class="person__role">DIRECTOR</p>
  </div>
  <div class="rule"></div>

  <ul class="contact">
    <li class="noicon"><span><span class="contact__label">ABN:</span> 71208349162</span></li>
    <li><span>0481-209-736</span>
      <svg viewBox="0 0 24 24" aria-hidden="true"><path d="M6.6 10.8a15.1 15.1 0 0 0 6.6 6.6l2.2-2.2c.3-.3.7-.4 1-.2 1.1.4 2.3.6 3.6.6.6 0 1 .4 1 1V20c0 .6-.4 1-1 1A17 17 0 0 1 3 4c0-.6.4-1 1-1h3.5c.6 0 1 .4 1 1 0 1.3.2 2.5.6 3.6.1.3 0 .7-.2 1z"/></svg></li>
    <li><span>brent@corvaneelectricalandcomms.example.com.au</span>
      <svg viewBox="0 0 24 24" aria-hidden="true"><path d="M3 5h18v14H3zm2 2v.5l7 4.5 7-4.5V7zm0 2.9V17h14V9.9l-7 4.5z"/></svg></li>
    <li><span>www.corvaneelectricalandcomms.example.com.au</span>
      <svg viewBox="0 0 24 24" aria-hidden="true"><circle cx="12" cy="12" r="9" fill="none" stroke="#f5a623" stroke-width="2"/><path d="M3 12h18M12 3c3 3 3 15 0 18M12 3c-3 3-3 15 0 18" fill="none" stroke="#f5a623" stroke-width="1.6"/></svg></li>
  </ul>

  <div class="wordmark">
    <span class="wordmark__dot"></span>
    <span class="wordmark__name">Corvane Electrical<br>and Communications</span>
  </div>

  <div class="band">
    <span class="band__cell band__left"></span>
    <span class="band__cell band__mid"></span>
    <span class="band__cell band__right"></span>
  </div>
  <p class="licence">Lic No: 418273D</p>
</section>

</body>
</html>
```